Summit Leadership Transformation Roadmap

I've included a mock up of what I like. This design needs to be made better. I like the top section layout. It needs 5 circles for:

Please create a webpage based on this design, but improve it. Use the letterhead and business card brand you created for me to make the brand look seamless.

I love the circles - please make 5 of them the same size (can be 1 lines)

Here is the text for the circles:

Headline: Your Guided Path to Transformation
Text
Step 1: The Initial Consultation
text
Step 2: Deep-Dive Discovery and Assessment
text
Step 3: Synthesis and Strategy Formulation
text
Step 4: The Strategic Debrief Session
Text
Step 5: Implementation and Ongoing Support
Text

Also, there are many sections to this page including:

Introduction
Copy
Copy
Bio
CTA
FAQ's

Please make it interesting.

Use the colors of the mockup and my website: Corwin Adeley.com
I am including my letterhead and business card for brand coherence.

Use the fonts on my website. CorwinAdeley.com

I will need all files to send to the developer. We must have ALL the art files.

see my website; CorwinAdeley.com

See my uploads

Must have
• all the design files

```html
<!DOCTYPE html>
<html lang="en">
<head>
<meta charset="utf-8">
<title>Summit Leadership Transformation</title>
<link href="https://fonts.googleapis.com/css2?family=Epilogue:wght@400;500;600&family=Montserrat:wght@400;500;600;700&display=swap" rel="stylesheet">
<style>
:root{
  --navy:#1b2a63;
  --navy-deep:#15214f;
  --gold:#ecc98a;
  --gold-dark:#c99a4f;
  --teal:#2e7fa3;
  --cream:#faf5ea;
  --ink:#1d1d1f;
  --muted:#555a66;
  --white:#ffffff;
}
*{margin:0;padding:0;box-sizing:border-box}
html,body{width:1200px;height:3667px;overflow:hidden;background:var(--white)}
body{font-family:"Montserrat",sans-serif;color:var(--ink)}
.page{position:relative;width:1200px;height:3667px;overflow:hidden}
.abs{position:absolute}
h1,h2,h3{font-family:"Epilogue",sans-serif;font-weight:500}
.btn{position:absolute;display:flex;align-items:center;justify-content:center;background:var(--gold);color:var(--navy-deep);font-weight:700;font-size:14px;letter-spacing:.3px;border-radius:30px;text-decoration:none;text-transform:uppercase}
.center-text{text-align:center;left:0;width:1200px}
.rule{position:absolute;height:3px;width:58px;background:var(--gold);left:571px}

/* hero */
.hero-photo{top:0;left:0;width:1200px;height:700px;background:linear-gradient(180deg,#3c4f8c 0%,#33447a 45%,#2a3560 100%)}
.topbar{top:0;left:0;width:1200px;height:40px;background:var(--navy-deep);color:var(--white);font-size:16px;font-weight:500;display:flex;align-items:center;justify-content:center}
.brand{top:62px;left:118px;display:flex;align-items:center;gap:10px;color:var(--white);font-size:16px;font-weight:600}
.brand-dot{width:14px;height:14px;border-radius:50%;background:var(--gold)}
.nav{top:73px;font-size:14px;color:var(--white);text-transform:uppercase;transform:translateX(-50%)}
.nav.active{color:var(--gold);text-decoration:underline;text-underline-offset:4px}
.hero-title{top:168px;font-size:50px;line-height:58px;color:var(--white)}
.hero-title span{color:var(--gold)}
.hero-sub{top:295px;font-size:20px;line-height:29px;color:var(--white)}

/* stats */
.stat{top:704px;width:300px;text-align:center;transform:translateX(-50%)}
.stat .num{font-family:"Epilogue",sans-serif;font-size:24px;font-weight:500;color:var(--navy)}
.stat .bar{width:44px;height:3px;background:var(--teal);margin:8px auto 18px}
.stat .label{font-size:16px;color:var(--ink)}

/* bio */
.portrait{left:131px;top:1049px;width:450px;height:450px;border-radius:50%;background:radial-gradient(circle at 45% 35%,#e9d2b6 0%,#b8936a 40%,#2a3152 78%);box-shadow:8px -6px 0 0 var(--gold)}
.bio-name{top:955px;left:611px;font-size:45px;color:var(--ink)}
.bio-rule{position:absolute;top:1033px;left:616px;width:58px;height:3px;background:var(--gold)}
.bio-text{left:616px;top:1060px;width:414px;font-size:13px;line-height:24px;color:var(--muted);text-align:justify}
.bio-text p+p{margin-top:24px}

/* path */
.path-title{top:1582px;font-size:36px;color:var(--ink)}
.step{top:1705px;width:180px;transform:translateX(-50%);text-align:center}
.step-disc{position:relative;width:120px;height:120px;margin:0 auto;border-radius:50%;background:radial-gradient(circle,#fbe7c1 0%,var(--gold) 70%);box-shadow:0 6px 10px rgba(0,0,0,.12)}
.step-inner{position:absolute;left:18px;top:18px;width:84px;height:84px;border-radius:50%;background:linear-gradient(160deg,#e2b670,var(--gold-dark));display:flex;align-items:center;justify-content:center}
.step-num{position:absolute;left:42px;top:-12px;width:36px;height:36px;border-radius:50%;background:var(--teal);color:var(--white);font-size:22px;font-weight:600;display:flex;align-items:center;justify-content:center;border:2px solid var(--white)}
.step-label{margin-top:18px;font-size:18px;line-height:27px;font-weight:500;color:var(--ink)}

/* seek */
.seek-title{top:2098px;font-size:36px;line-height:44px;color:var(--white)}
.seek-text{top:2292px;left:180px;width:840px;font-size:13.5px;line-height:24px;color:var(--white);text-align:center}
.seek-text strong{color:var(--gold);font-weight:600}
.seek-text p+p{margin-top:24px}

/* faq */
.faq-title{top:2744px;font-size:36px;color:var(--ink)}
.faq-item{width:452px;height:54px;border:1.5px solid #e4e4e8;border-radius:6px;background:var(--white);box-shadow:0 3px 6px rgba(0,0,0,.06);display:flex;align-items:center;justify-content:space-between;padding:0 20px;font-size:14px;font-weight:500}
.faq-item b{font-size:24px;font-weight:600}

/* footer */
.foot-head{font-family:"Epilogue",sans-serif;font-size:19px;font-weight:600;color:var(--ink);letter-spacing:.5px}
.foot-list{list-style:none;margin-top:14px}
.foot-list li{font-size:15px;color:var(--muted);height:34px;display:flex;align-items:center;gap:8px}
.foot-list li svg{flex:none}
.foot-brand{left:120px;top:3440px;width:266px;text-align:center}
.foot-brand .name{display:flex;align-items:center;justify-content:center;gap:8px;font-size:12px;font-weight:700;color:var(--navy)}
.foot-brand .name i{width:10px;height:10px;border-radius:50%;background:var(--gold);display:block}
.foot-brand .small{font-size:11px;line-height:20px;color:var(--muted);margin-top:4px}
.news-input{left:848px;top:3456px;width:211px;height:44px;border:1px solid #dcdcdc;background:var(--white);border-radius:4px;font-size:13px;color:var(--muted);display:flex;align-items:center;padding-left:10px}
.news-send{left:1011px;top:3456px;width:48px;height:44px;background:var(--navy-deep);border-radius:6px;display:flex;align-items:center;justify-content:center}
</style>
</head>
<body>
<div class="page">

  <!-- HERO -->
  <div class="abs hero-photo" role="img" aria-label="Photo of an audience of professionals attending a leadership seminar"></div>
  <svg class="abs" style="top:0;left:0" width="1200" height="1000" viewBox="0 0 1200 1000" aria-hidden="true">
    <path d="M0,555 Q600,730 1200,530 L1200,1000 L0,1000 Z" fill="#ecc98a"/>
    <path d="M0,960 Q600,730 1200,960 L1200,1000 L0,1000 Z" fill="#ffffff"/>
  </svg>
  <div class="abs topbar">Summit Leadership Transformation and Organization Development</div>
  <div class="abs brand"><span class="brand-dot"></span>Summit Leadership</div>
  <div class="abs nav active" style="left:430px">Home</div>
  <div class="abs nav" style="left:530px">Coaching</div>
  <div class="abs nav" style="left:643px">Retreats</div>
  <div class="abs nav" style="left:743px">About</div>
  <div class="abs nav" style="left:840px">Insights</div>
  <a class="btn" style="left:935px;top:60px;width:139px;height:43px">Contact Us</a>

  <h1 class="abs center-text hero-title">Support Your Leadership<br>Efforts with <span>Summit Coaching</span></h1>
  <p class="abs center-text hero-sub">Introducing Summit Leadership Coaching<br>and Organization Development</p>
  <a class="btn" style="left:471px;top:374px;width:256px;height:43px">Book a Discovery Call</a>

  <!-- STATS -->
  <div class="abs stat" style="left:223px"><div class="num">25 Years</div><div class="bar"></div><div class="label">Experience</div></div>
  <div class="abs stat" style="left:473px"><div class="num">15,000+</div><div class="bar"></div><div class="label">Transformational Sessions</div></div>
  <div class="abs stat" style="left:723px"><div class="num">#1 National</div><div class="bar"></div><div class="label">Bestselling Author</div></div>
  <div class="abs stat" style="left:972px"><div class="num">700+</div><div class="bar"></div><div class="label">Licensable Training Materials</div></div>

  <!-- BIO -->
  <div class="abs portrait" role="img" aria-label="Portrait photo of Corwin Adeley, leadership coach"></div>
  <h2 class="abs bio-name">Corwin Adeley</h2>
  <div class="bio-rule"></div>
  <div class="abs bio-text">
    <p>As a top leader, you deserve an elite partnership designed exclusively for you—especially when you need a woman you can count on. With a perspective rooted in both wisdom and empathy, I offer insights, intuition, and support that many male coaches simply cannot replicate.</p>
    <p>My mission is to guide high-performing leaders and their teams toward a state of peak performance defined by stress-free resilience, heightened productivity, and effortless flow. I founded Corwin Adeley International to provide effective, accelerated training that unlocks the highest levels of human potential. I am especially passionate about empowering executives and senior-level management to lead with clarity, impact, and well-being.</p>
  </div>
  <a class="btn" style="left:620px;top:1428px;width:257px;height:43px">Book a Discovery Call</a>

  <!-- PATH -->
  <h2 class="abs center-text path-title">Your Guided Path to Transformation</h2>
  <div class="rule" style="top:1651px"></div>

  <svg class="abs" style="top:1730px;left:0" width="1200" height="70" viewBox="0 0 1200 70" aria-hidden="true" fill="none" stroke="#6b6f7a" stroke-width="2" stroke-linecap="round">
    <path d="M248,47 Q285,62 318,43"/><path d="M308,40 L318,43 L314,53"/>
    <path d="M458,30 Q495,12 528,34"/><path d="M518,34 L528,34 L526,24"/>
    <path d="M670,47 Q707,62 740,43"/><path d="M730,40 L740,43 L736,53"/>
    <path d="M882,30 Q919,12 952,34"/><path d="M942,34 L952,34 L950,24"/>
  </svg>

  <div class="abs step" style="left:177px">
    <div class="step-disc"><div class="step-inner">
      <svg width="46" height="46" viewBox="0 0 46 46" fill="none" stroke="#3a2a14" stroke-width="2"><circle cx="14" cy="14" r="5"/><circle cx="32" cy="14" r="5"/><path d="M6,34 V26 Q14,20 22,26 V34 M24,34 V26 Q32,20 40,26 V34 M4,36 H42"/></svg>
    </div><div class="step-num">1</div></div>
    <div class="step-label">The Initial<br>Consultation</div>
  </div>
  <div class="abs step" style="left:387px">
    <div class="step-disc"><div class="step-inner">
      <svg width="46" height="46" viewBox="0 0 46 46" fill="none" stroke="#3a2a14" stroke-width="2"><path d="M16,30 Q8,24 10,15 Q13,6 22,6 Q30,7 31,14"/><path d="M16,30 V36 H22"/><circle cx="30" cy="24" r="8"/><path d="M36,30 L42,36"/></svg>
    </div><div class="step-num">2</div></div>
    <div class="step-label">Deep-Dive<br>Discovery and<br>Assessment</div>
  </div>
  <div class="abs step" style="left:598px">
    <div class="step-disc"><div class="step-inner">
      <svg width="46" height="46" viewBox="0 0 46 46" fill="none" stroke="#3a2a14" stroke-width="2"><rect x="10" y="6" width="26" height="34" rx="2"/><path d="M15,14 L17,16 L20,12 M23,14 H31 M15,22 L17,24 L20,20 M23,22 H31 M15,30 L17,32 L20,28 M23,30 H31"/></svg>
    </div><div class="step-num">3</div></div>
    <div class="step-label">Synthesis and<br>Strategy<br>Formulation</div>
  </div>
  <div class="abs step" style="left:809px">
    <div class="step-disc"><div class="step-inner">
      <svg width="46" height="46" viewBox="0 0 46 46" fill="none" stroke="#3a2a14" stroke-width="2"><circle cx="23" cy="12" r="4"/><circle cx="11" cy="18" r="4"/><circle cx="35" cy="18" r="4"/><path d="M6,30 H40 M10,30 V40 M36,30 V40 M16,30 Q16,22 23,20 Q30,22 30,30"/></svg>
    </div><div class="step-num">4</div></div>
    <div class="step-label">The Strategic<br>Debrief<br>Session</div>
  </div>
  <div class="abs step" style="left:1019px">
    <div class="step-disc"><div class="step-inner">
      <svg width="46" height="46" viewBox="0 0 46 46" fill="none" stroke="#3a2a14" stroke-width="2"><path d="M12,30 Q5,24 8,15 Q12,8 19,9 Q26,12 25,20 Q24,25 20,30 Z"/><path d="M13,34 H19 M14,38 H18"/><circle cx="33" cy="30" r="5"/><circle cx="33" cy="30" r="9" stroke-dasharray="3 3"/><path d="M30,8 H38 V16"/></svg>
    </div><div class="step-num">5</div></div>
    <div class="step-label">Implementation<br>and Ongoing<br>Support Text</div>
  </div>

  <!-- SEEKING -->
  <svg class="abs" style="top:1880px;left:0" width="1200" height="800" viewBox="0 0 1200 800" role="img" aria-label="Photo of women leaders in a workshop, tinted navy">
    <defs><linearGradient id="navyBand" x1="0" y1="0" x2="0" y2="1"><stop offset="0" stop-color="#1b2a63"/><stop offset="1" stop-color="#243574"/></linearGradient></defs>
    <path d="M0,235 Q600,5 1200,240 L1200,675 Q600,890 0,675 Z" fill="url(#navyBand)"/>
  </svg>
  <h2 class="abs center-text seek-title">Are you seeking a Leadership Coach and<br>Organization Development Specialist to<br>elevate your leadership impact?</h2>
  <div class="rule" style="top:2261px"></div>
  <div class="abs seek-text">
    <p><strong>Summit Coaching with Corwin Adeley</strong> — Your organization—and its challenges—are unlike any other. Generic training can only take your leaders so far. To achieve the profound, lasting impact your vision demands, you need a solution crafted specifically for you.</p>
    <p>Corwin Adeley creates transformative, custom leadership retreats for management teams in the Greater Seattle Area. Through Summit Coaching, we provide the deep guidance and tailored strategies your leaders need to overcome obstacles, foster unity, and achieve exceptional, lasting results—only possible through a uniquely designed, custom-built program.</p>
  </div>
  <a class="btn" style="left:471px;top:2494px;width:256px;height:43px">Book a Discovery Call</a>

  <!-- FOOTER BACKGROUND -->
  <svg class="abs" style="top:3100px;left:0" width="1200" height="567" viewBox="0 0 1200 567" aria-hidden="true">
    <rect width="1200" height="567" fill="#faf5ea"/>
    <path d="M0,0 H1200 V50 Q600,270 0,50 Z" fill="#ffffff"/>
  </svg>

  <!-- FAQ -->
  <h2 class="abs center-text faq-title">FAQ's</h2>
  <div class="rule" style="top:2803px"></div>
  <div class="abs faq-item" style="left:128px;top:2831px">Lorem Ipsum is simply dummy text<b>+</b></div>
  <div class="abs faq-item" style="left:616px;top:2831px">Lorem Ipsum is simply dummy text<b>+</b></div>
  <div class="abs faq-item" style="left:128px;top:2903px">Lorem Ipsum is simply dummy text<b>+</b></div>
  <div class="abs faq-item" style="left:616px;top:2903px">Lorem Ipsum is simply dummy text<b>+</b></div>
  <div class="abs faq-item" style="left:128px;top:2975px">Lorem Ipsum is simply dummy text<b>+</b></div>
  <div class="abs faq-item" style="left:616px;top:2975px">Lorem Ipsum is simply dummy text<b>+</b></div>
  <div class="abs faq-item" style="left:128px;top:3048px">Lorem Ipsum is simply dummy text<b>+</b></div>
  <div class="abs faq-item" style="left:616px;top:3048px">Lorem Ipsum is simply dummy text<b>+</b></div>
  <a class="btn" style="left:507px;top:3136px;width:180px;height:43px">Contact Us</a>

  <!-- FOOTER -->
  <div class="abs foot-brand">
    <div class="name"><i></i>Summit Leadership Transformation</div>
    <div class="small">is a trade name owned by<br>Corwin Adeley International<br>and The Resonant Wellness Institute.</div>
  </div>

  <div class="abs" style="left:416px;top:3343px">
    <div class="foot-head">MAIN LINKS</div>
    <ul class="foot-list">
      <li><svg width="14" height="12" viewBox="0 0 14 12"><path d="M0,6 H11 M7,1 L12,6 L7,11" stroke="#1d1d1f" stroke-width="2" fill="none"/></svg>Home</li>
      <li><svg width="14" height="12" viewBox="0 0 14 12"><path d="M0,6 H11 M7,1 L12,6 L7,11" stroke="#1d1d1f" stroke-width="2" fill="none"/></svg>About</li>
      <li><svg width="14" height="12" viewBox="0 0 14 12"><path d="M0,6 H11 M7,1 L12,6 L7,11" stroke="#1d1d1f" stroke-width="2" fill="none"/></svg>2026 Retreat</li>
      <li><svg width="14" height="12" viewBox="0 0 14 12"><path d="M0,6 H11 M7,1 L12,6 L7,11" stroke="#1d1d1f" stroke-width="2" fill="none"/></svg>Insights</li>
    </ul>
  </div>
  <div class="abs" style="left:592px;top:3343px">
    <div class="foot-head">SUPPORT</div>
    <ul class="foot-list">
      <li><svg width="14" height="12" viewBox="0 0 14 12"><path d="M0,6 H11 M7,1 L12,6 L7,11" stroke="#1d1d1f" stroke-width="2" fill="none"/></svg>Terms &amp; Policies</li>
      <li><svg width="14" height="12" viewBox="0 0 14 12"><path d="M0,6 H11 M7,1 L12,6 L7,11" stroke="#1d1d1f" stroke-width="2" fill="none"/></svg>Membership Agreement</li>
      <li><svg width="14" height="12" viewBox="0 0 14 12"><path d="M0,6 H11 M7,1 L12,6 L7,11" stroke="#1d1d1f" stroke-width="2" fill="none"/></svg>Contact</li>
    </ul>
  </div>
  <div class="abs" style="left:851px;top:3343px">
    <div class="foot-head">NEWSLETTER SIGN UP</div>
    <p style="margin-top:20px;font-size:12px;line-height:22px;color:var(--muted)">We Will Notify You Of Any<br>Important News</p>
  </div>
  <div class="abs news-input">Your Email Address</div>
  <div class="abs news-send"><svg width="24" height="24" viewBox="0 0 24 24" fill="none" stroke="#ffffff" stroke-width="1.8" stroke-linejoin="round"><path d="M22,2 L2,10 L11,13 L14,22 Z M22,2 L11,13"/></svg></div>

  <div class="abs" style="left:100px;top:3592px;width:953px;height:1px;background:#2a2a2a"></div>
  <p class="abs center-text" style="top:3612px;font-size:13px;color:var(--ink)">Copyright © 2025. All rights reserved.</p>

</div>
</body>
</html>
```